New business card/stationary for a consulting company

I am looking for a clean and very professional looking business card for my consulting company as well as corresponding stationary. I am uploading our logo. I like simple and powerful for the feel. No graphics but I am open on everything else. Below is my contact information but would like the final to be in a version I can add my employees information into and print. Thank you.

Daniel Whitcombe
dan@ferncliffadvisory.com
2870 North 9th Avenue, Summit Floor, Elm Ridge, Illinois 60531
www.ferncliffadvisory.com

Industry/Entity Type

Consulting

Contact Information for Business Card

Daniel Whitcombe
dan@ferncliffadvisory.com
www.ferncliffadvisory.com

Font styles to use
Serif
Sans Serif

Requirements
Must have
• Our logo and the business card details.
Nice to have
• our website www.ferncliffadvisory.com

```html
<!DOCTYPE html>
<html lang="en">
<head>
<meta charset="utf-8">
<title>Ferncliff Advisory — Business Card</title>
<link rel="stylesheet" href="https://fonts.googleapis.com/css2?family=Cinzel:wght@400;700&family=Raleway:wght@400&display=swap">
<style>
  :root {
    --navy: #2d2a78;
    --ink: #2d2a78;
    --paper: #ffffff;
    --backdrop: #e6e7ea;
    --rule: #6b689e;
  }
  * { box-sizing: border-box; margin: 0; padding: 0; }
  html, body {
    width: 1200px;
    height: 674px;
    overflow: hidden;
    background: var(--backdrop);
  }
  .card {
    position: absolute;
    left: 75px;
    top: 37px;
    width: 1050px;
    height: 600px;
    background: var(--paper);
    box-shadow: 0 6px 22px rgba(0,0,0,0.12);
    overflow: hidden;
  }
  .brand {
    position: absolute;
    left: 60px;
    top: 170px;
    width: 400px;
    text-align: center;
  }
  .brand-mark {
    display: block;
    width: 96px;
    height: 58px;
    margin: 0 auto 14px;
    background: var(--navy);
  }
  .brand-name {
    font-family: "Raleway", sans-serif;
    font-weight: 400;
    font-size: 33px;
    letter-spacing: 1.5px;
    color: var(--ink);
    text-transform: uppercase;
    white-space: nowrap;
  }
  .divider {
    position: absolute;
    left: 528px;
    top: 140px;
    width: 2px;
    height: 250px;
    background: var(--rule);
  }
  .contact {
    position: absolute;
    left: 566px;
    top: 150px;
    width: 460px;
    color: var(--ink);
  }
  .person-name {
    font-family: "Cinzel", serif;
    font-weight: 700;
    font-size: 36px;
    letter-spacing: 1px;
    margin-bottom: 22px;
    white-space: nowrap;
  }
  .contact-line {
    display: flex;
    align-items: flex-start;
    gap: 12px;
    font-family: "Cinzel", serif;
    font-weight: 400;
    font-size: 16px;
    line-height: 1.45;
    letter-spacing: 0.5px;
    margin-bottom: 16px;
  }
  .contact-line svg {
    flex: 0 0 18px;
    width: 18px;
    height: 18px;
    margin-top: 2px;
    fill: var(--ink);
  }
  .contact-line.is-email { text-transform: lowercase; }
  .band {
    position: absolute;
    left: 0;
    bottom: 0;
    width: 100%;
    height: 128px;
    background: var(--navy);
  }
</style>
</head>
<body>
  <div class="card">
    <div class="brand">
      <span class="brand-mark"></span>
      <div class="brand-name">Ferncliff Advisory</div>
    </div>

    <div class="divider"></div>

    <div class="contact">
      <div class="person-name">Daniel Whitcombe</div>

      <div class="contact-line is-address">
        <svg viewBox="0 0 24 24" aria-hidden="true"><path d="M12 2a7 7 0 0 0-7 7c0 5.2 7 13 7 13s7-7.8 7-13a7 7 0 0 0-7-7zm0 9.5A2.5 2.5 0 1 1 12 6.5a2.5 2.5 0 0 1 0 5z"/></svg>
        <span>2870 North 9th Avenue, Summit<br>Floor, Elm Ridge, Illinois 60531</span>
      </div>

      <div class="contact-line is-email">
        <svg viewBox="0 0 24 24" aria-hidden="true"><path d="M3 5h18v14H3V5zm2 2v.5l7 5 7-5V7H5zm0 3v7h14v-7l-7 5-7-5z"/></svg>
        <span>dan@ferncliffadvisory.com</span>
      </div>

      <div class="contact-line is-web">
        <svg viewBox="0 0 24 24" aria-hidden="true"><path d="M12 2a10 10 0 1 0 0 20 10 10 0 0 0 0-20zm6.9 9h-3a15 15 0 0 0-1.2-5.4A8 8 0 0 1 18.9 11zM12 4.1c.9 1.2 1.7 3.5 1.9 6.9h-3.8c.2-3.4 1-5.7 1.9-6.9zM9.3 5.6A15 15 0 0 0 8.1 11h-3a8 8 0 0 1 4.2-5.4zM5.1 13h3a15 15 0 0 0 1.2 5.4A8 8 0 0 1 5.1 13zm6.9 6.9c-.9-1.2-1.7-3.5-1.9-6.9h3.8c-.2 3.4-1 5.7-1.9 6.9zm2.7-1.5a15 15 0 0 0 1.2-5.4h3a8 8 0 0 1-4.2 5.4z"/></svg>
        <span>www.ferncliffadvisory.com</span>
      </div>
    </div>

    <div class="band"></div>
  </div>
</body>
</html>
```